Website redesign www.marigoldlawpc.com law firm site

Need to redesign the website that I currently have to look more modern and professional. Would also like to be able to make updates and post without having a huge hassle. See current www.marigoldlawpc.com. I just think that it looks very immature and it's very templated there's no ability for me to make posts or Add links or anything like that

Target Market(s)

California people looking for a powerhouse attorney in

Industry/Entity Type

Legal

Number of Pages Required

3 page

Font styles to use
Serif
Sans Serif

Colors
ec1f27
000000
ffffff

Requirements
Must have
• Must be mobile friendly. Must look professional and have ability to post links to other websites. Must have ability to post blogs or articles. Would like to be able to read my FeeTrove account and also have the ability to upload forms for people to download
Nice to have
• Simple design easy to use and not cluttered with too much text

```html
<!DOCTYPE html>
<html lang="en">
<head>
<meta charset="utf-8">
<title>Marigold Law P.C. — Chico California Attorney</title>
<link href="https://fonts.googleapis.com/css2?family=Cinzel:wght@400;700&family=Open+Sans:wght@400;600;700&display=swap" rel="stylesheet">
<style>
:root{
  --red:#ec1f27;
  --red-dark:#c8161d;
  --black:#000000;
  --white:#ffffff;
  --ink:#333333;
  --muted:#666666;
  --line:#dddddd;
  --pale:#f2f2f2;
  --footer:#1e1e1e;
  --footer-line:#333333;
  --badge-blue:#2a4a80;
  --badge-grey:#8a8a8a;
  --badge-slate:#7a8a9c;
}
*{box-sizing:border-box;margin:0;padding:0}
html,body{width:1200px;height:2748px;overflow:hidden;background:var(--white)}
body{position:relative;font-family:"Open Sans",Arial,sans-serif;color:var(--ink)}
.abs{position:absolute}
.btn{position:absolute;background:var(--red);color:var(--white);font-size:12px;display:flex;align-items:center;justify-content:center;border-radius:2px}

/* header */
.site-header{position:absolute;left:0;top:0;width:1200px;height:135px;border-top:4px solid var(--red);background:var(--white)}
.brand{position:absolute;left:100px;top:30px;width:245px;text-align:center;color:var(--red-dark)}
.brand-name{font-family:"Cinzel",Georgia,serif;font-size:29px;font-weight:700;line-height:1;letter-spacing:.3px;white-space:nowrap}
.brand-rule{height:2px;background:var(--red-dark);margin:8px 0 2px}
.brand-sub{font-family:"Cinzel",Georgia,serif;font-size:13px;font-weight:700}
.header-phone{position:absolute;left:808px;top:30px;display:flex;align-items:center;gap:10px;font-family:"Cinzel",Georgia,serif;font-size:19px;color:var(--ink)}
.header-phone .ring{width:32px;height:32px;border:2px solid var(--red);border-radius:50%;display:flex;align-items:center;justify-content:center}
.social{position:absolute;display:flex;gap:6px}
.social span{width:31px;height:31px;border-radius:50%;display:block}
.main-nav{position:absolute;left:418px;top:80px;display:flex;height:40px;border-bottom:1px solid var(--line)}
.main-nav a{display:flex;align-items:center;padding:0 14px;font-family:"Cinzel",Georgia,serif;font-size:13px;color:var(--ink);text-decoration:none;position:relative;letter-spacing:.3px;white-space:nowrap}
.main-nav a + a::before{content:"";position:absolute;left:0;top:4px;height:32px;border-left:1px solid #cccccc;transform:skewX(-20deg)}
.main-nav a.active{border-bottom:3px solid var(--red);margin-bottom:-1px}

/* hero */
.hero{position:absolute;left:0;top:135px;width:1200px;height:515px;background:linear-gradient(100deg,#6b6f74 0%,#8d8f91 22%,#5a4234 48%,#3b2a21 75%,#2b1e18 100%)}
.hero-shade{position:absolute;inset:0;background:linear-gradient(90deg,rgba(0,0,0,.35),rgba(0,0,0,.05) 60%,rgba(0,0,0,.25))}
.hero-title{position:absolute;left:100px;top:176px;color:var(--white);font-family:"Cinzel",Georgia,serif;font-size:29px;line-height:33px;letter-spacing:.5px;white-space:nowrap}
.hero-rule{position:absolute;left:100px;top:243px;width:448px;height:2px;background:var(--white)}
.hero-text{position:absolute;left:100px;top:250px;width:560px;color:var(--white);font-size:13px;line-height:23px}
.arrow{position:absolute;top:232px}
.quick{position:absolute;left:808px;top:75px;width:295px;height:365px;background:rgba(40,28,22,.82)}
.quick-head{height:48px;background:var(--red);color:var(--white);font-family:"Cinzel",Georgia,serif;font-size:21px;display:flex;align-items:center;padding-left:16px}
.field{position:absolute;left:14px;width:270px;height:36px;border:1px solid rgba(255,255,255,.45);display:flex;align-items:center;gap:10px;padding-left:12px;color:#e6e6e6;font-size:11.5px}
.field.tall{height:82px;align-items:flex-start;padding-top:10px}

/* welcome */
.video{position:absolute;left:100px;top:708px;width:432px;height:282px;border:4px solid #e2e2e2;box-shadow:0 1px 4px rgba(0,0,0,.2);background:radial-gradient(ellipse at center,#f2eeee 0%,#d9d6d6 60%,#c9c6c6 100%)}
.play{position:absolute;left:187px;top:117px}
.section-title{font-family:"Cinzel",Georgia,serif;color:var(--red);font-size:29px;letter-spacing:.3px;white-space:nowrap}
.title-rule{height:2px;background:var(--red)}
.welcome-text{position:absolute;left:550px;top:765px;width:555px;font-size:12.3px;line-height:22.3px;color:#555555}

/* practice */
.practice{position:absolute;left:0;top:1045px;width:1200px;height:463px;background:var(--pale)}
.center-title{position:absolute;left:0;width:1200px;text-align:center}
.practice-intro{position:absolute;left:130px;top:140px;width:940px;text-align:center;font-size:12px;line-height:22px;color:#555555}
.area{position:absolute;top:232px;width:226px;text-align:center}
.area svg{display:block;margin:0 auto}
.area h3{font-family:"Cinzel",Georgia,serif;font-weight:700;font-size:13px;color:var(--ink);margin-top:12px;letter-spacing:.5px}
.area p{font-size:11.8px;line-height:20px;color:#555555;margin-top:3px}

/* blog */
.card{position:absolute;top:1633px;width:231px;height:335px;border:1px solid var(--line);background:var(--white)}
.card-img{height:170px;margin:3px;border:1px solid #e5e5e5}
.card h4{font-family:"Open Sans",Arial,sans-serif;font-weight:700;font-size:12.5px;color:var(--ink);margin:15px 0 0 12px;letter-spacing:.3px}
.meta{display:flex;align-items:center;gap:6px;margin:8px 0 0 12px;font-size:11.5px;color:#555555}
.card p{margin:5px 12px 0;font-size:12px;line-height:20.5px;color:#444444}

/* reviews */
.reviews{position:absolute;left:0;top:2010px;width:1200px;height:420px;background:var(--pale)}
.quote-box{position:absolute;left:100px;top:125px;width:478px;height:118px;background:#f7f7f7;border:1px solid #e4e4e4;padding:16px 30px 0 40px;font-size:12px;line-height:24px;font-style:italic;color:#555555}
.quote-box .mark{position:absolute;font-family:Georgia,serif;font-size:40px;color:#cccccc;font-style:normal}
.avatar{position:absolute;left:105px;top:275px;width:86px;height:86px;border-radius:50%;border:3px solid var(--white);box-shadow:0 0 0 1px #dddddd;background:linear-gradient(180deg,#c9b7a8,#47525e)}
.reviewer{position:absolute;left:220px;top:292px;font-size:12px;color:var(--ink)}
.reviewer b{display:block;color:var(--red);font-size:12.5px;margin-bottom:4px}
.ratings-box{position:absolute;left:655px;top:120px;width:448px;height:255px;background:var(--white);border:1px solid #e4e4e4}
.badge{position:absolute}
.badge-rating{left:34px;top:40px;width:100px;height:100px;border-radius:50%;background:var(--badge-blue)}
.badge-bar{left:193px;top:30px;width:118px;height:118px;border-radius:50%;background:var(--badge-grey)}
.badge-directory{left:36px;top:178px;width:236px;height:44px;background:var(--badge-slate)}

/* footer */
.site-footer{position:absolute;left:0;top:2430px;width:1200px;height:318px;background:var(--footer);color:#dddddd}
.foot-head{position:absolute;top:32px;font-family:"Cinzel",Georgia,serif;font-size:17px;color:var(--white);letter-spacing:.5px}
.foot-list{position:absolute;top:66px;list-style:none;font-size:12px;line-height:24px}
.foot-list li::before{content:"›";margin-right:8px;color:var(--white)}
.foot-contact{position:absolute;left:618px;top:66px;font-size:12px;line-height:17px}
.foot-contact .row{display:flex;gap:14px;align-items:flex-start}
.bottom-bar{position:absolute;left:0;top:262px;width:1200px;border-top:1px solid var(--footer-line)}
.copyright{position:absolute;left:100px;top:283px;font-size:12px;color:#dddddd}
</style>
</head>
<body>

<header class="site-header">
  <div class="brand">
    <div class="brand-name">Marigold Law</div>
    <div class="brand-rule"></div>
    <div class="brand-sub">P.C</div>
  </div>
  <div class="header-phone">
    <span class="ring"><svg width="14" height="14" viewBox="0 0 24 24"><path fill="#ec1f27" d="M6.6 10.8a15 15 0 0 0 6.6 6.6l2.2-2.2c.3-.3.7-.4 1-.2 1.1.4 2.3.6 3.6.6.6 0 1 .4 1 1V20c0 .6-.4 1-1 1A17 17 0 0 1 3 4c0-.6.4-1 1-1h3.5c.6 0 1 .4 1 1 0 1.3.2 2.5.6 3.6.1.3 0 .7-.2 1z"/></svg></span>
    (555) 014-2290
  </div>
  <div class="social" style="left:990px;top:30px">
    <span style="background:#4a67ad"></span><span style="background:#4aa3df"></span><span style="background:#d12121"></span>
  </div>
  <nav class="main-nav">
    <a class="active">HOME</a><a>ATTORNEY PROFILE</a><a>PRACTICE AREAS</a><a>CLIENT REVIEWS</a><a>LINKS</a><a>CONTACT US</a>
  </nav>
</header>

<section class="hero">
  <div class="abs" style="inset:0" role="img" aria-label="Photo of a model house beside a wooden judge's gavel"></div>
  <div class="hero-shade"></div>
  <svg class="arrow" style="left:38px" width="16" height="50" viewBox="0 0 16 50"><path d="M14 2 2 25l12 23" fill="none" stroke="#ffffff" stroke-opacity=".7" stroke-width="2"/></svg>
  <svg class="arrow" style="left:1146px" width="16" height="50" viewBox="0 0 16 50"><path d="M2 2l12 23L2 48" fill="none" stroke="#ffffff" stroke-opacity=".7" stroke-width="2"/></svg>
  <h1 class="hero-title">MARIGOLD LAW, P.C.<br>CHICO CALIFORNIA ATTORNEY</h1>
  <div class="hero-rule"></div>
  <p class="hero-text">Marigold Law P.C. is owned by Dana R. Marigold, a dedicated and caring professional who uses her broad range of skills as a California lawyer to bring consumers and business</p>
  <div class="btn" style="left:97px;top:312px;width:145px;height:45px">View More Info</div>

  <form class="quick">
    <div class="quick-head">QUICK CONTACT</div>
    <div class="field" style="top:65px"><svg width="11" height="12" viewBox="0 0 11 12"><circle cx="5.5" cy="3" r="3" fill="#fff"/><path d="M0 12a5.5 5 0 0 1 11 0z" fill="#fff"/></svg>Enter your name</div>
    <div class="field" style="top:112px"><svg width="12" height="9" viewBox="0 0 12 9"><rect width="12" height="9" fill="#fff"/><path d="M0 0l6 5 6-5" fill="none" stroke="#333" stroke-width="1"/></svg>Email Number</div>
    <div class="field" style="top:161px"><svg width="10" height="12" viewBox="0 0 10 12"><path d="M0 0h7l3 3v9H0z" fill="#fff"/></svg>Subject</div>
    <div class="field tall" style="top:212px"><svg width="12" height="12" viewBox="0 0 12 12"><path d="M1 11l1-3 7-7 2 2-7 7z" fill="#fff"/></svg>Your Message</div>
    <div class="btn" style="left:14px;top:305px;width:125px;height:36px;font-size:11.5px">Call to Action</div>
  </form>
</section>

<section>
  <div class="video" role="img" aria-label="Word cloud illustration centred on the words criminal law">
    <svg class="play" width="50" height="36" viewBox="0 0 50 36"><rect width="50" height="36" rx="9" fill="#ec1f27"/><path d="M19 10l14 8-14 8z" fill="#fff"/></svg>
  </div>
  <h2 class="section-title abs" style="left:550px;top:704px;font-size:26px">WELCOME TO MARIGOLD LAW PC</h2>
  <div class="title-rule abs" style="left:550px;top:745px;width:225px"></div>
  <p class="welcome-text">Marigold Law P.C. is owned by Dana R. Marigold, a dedicated and caring professional who uses her broad range of skills as a California lawyer to bring consumers and business owners exceptionally strong legal representation that achieves best results. She works with people from across the northern region of California, from the Northern border to the Central Valley region. They bring her legal concerns and problems that occur in many areas of law, including Real Estate, Family law, Business Law, Bankruptcy, Criminal Law and Civil Litigation.Marigold Law P.C. is owned by Dana R. Marigold, a dedicated and caring professional who uses her broad range of skills</p>
  <div class="btn" style="left:550px;top:952px;width:124px;height:36px">View More Info</div>
</section>

<section class="practice">
  <h2 class="section-title center-title" style="top:68px">OUR PRACTICE AREAS</h2>
  <div class="title-rule abs" style="left:438px;top:118px;width:324px"></div>
  <p class="practice-intro">To provide personalized, affordable and thorough legal services to everyone who needs representation, Attorney Dana Marigold also created an in-house self-help clinic for people who want low-cost document preparation services that include attorney oversight and review.</p>

  <div class="area" style="left:107px">
    <svg width="70" height="60" viewBox="0 0 70 60"><path d="M25 14V8h20v6" fill="none" stroke="#ec1f27" stroke-width="4"/><rect x="5" y="15" width="60" height="40" fill="none" stroke="#ec1f27" stroke-width="4"/><path d="M5 30h60" stroke="#ec1f27" stroke-width="3"/><rect x="30" y="26" width="10" height="8" fill="#ec1f27"/></svg>
    <h3>BUSINESS LAW</h3>
    <p>Small and medium-sized businesses have many of the same legal issues that affect large businesses, such as...</p>
  </div>
  <div class="area" style="left:364px">
    <svg width="70" height="60" viewBox="0 0 70 60"><path d="M5 30 35 5l30 25" fill="none" stroke="#ec1f27" stroke-width="4"/><path d="M13 25v32h44V25" fill="none" stroke="#ec1f27" stroke-width="4"/><rect x="24" y="32" width="16" height="7" transform="rotate(-35 32 35)" fill="#ec1f27"/><path d="M36 38l10 12" stroke="#ec1f27" stroke-width="4"/><rect x="22" y="49" width="18" height="4" fill="#ec1f27"/></svg>
    <h3>REAL ESTATE LAW</h3>
    <p>At Marigold Law P.C., we help Californians who need legal advice and represent for Real Estate Law activities, such as...</p>
  </div>
  <div class="area" style="left:611px">
    <svg width="70" height="60" viewBox="0 0 70 60"><circle cx="42" cy="10" r="8" fill="#ec1f27"/><path d="M39 10h6" stroke="#fff" stroke-width="2"/><ellipse cx="34" cy="36" rx="26" ry="18" fill="#ec1f27"/><rect x="16" y="48" width="8" height="10" fill="#ec1f27"/><rect x="42" y="48" width="8" height="10" fill="#ec1f27"/><path d="M59 32h7v8h-7" fill="#ec1f27"/><circle cx="50" cy="30" r="2" fill="#fff"/></svg>
    <h3>BANKRUPTCY</h3>
    <p>If your finances are dwindling to the point where you can no longer pay your bills, and you are getting...</p>
  </div>
  <div class="area" style="left:872px">
    <svg width="70" height="60" viewBox="0 0 70 60"><circle cx="25" cy="8" r="6" fill="#ec1f27"/><circle cx="45" cy="8" r="6" fill="#ec1f27"/><path d="M17 17h16v22h-3v19h-10V39h-3z" fill="#ec1f27"/><path d="M37 17h16l4 22h-5v19h-10V39h-5z" fill="#ec1f27"/></svg>
    <h3>FAMILY LAW</h3>
    <p>Family Law is one area of legal concern that brings many people in to see our experienced Chico Family Law...</p>
  </div>
</section>

<section>
  <h2 class="section-title center-title" style="top:1553px">LATEST BLOG</h2>
  <div class="title-rule abs" style="left:502px;top:1598px;width:196px"></div>

  <article class="card" style="left:88px">
    <div class="card-img" role="img" aria-label="Photo of a person in a suit stamping a document" style="background:linear-gradient(135deg,#2a3442,#8a97a6 60%,#e9eaec)"></div>
    <h4>FAMILY LAW</h4>
    <div class="meta"><svg width="11" height="11" viewBox="0 0 11 11"><rect y="1.5" width="11" height="9.5" fill="#555"/><rect x="1" y="4" width="9" height="6" fill="#fff"/></svg>27 March 2014 <svg style="margin-left:6px" width="13" height="11" viewBox="0 0 13 11"><ellipse cx="6.5" cy="4.5" rx="6.5" ry="4.5" fill="#555"/><path d="M2 7l-1 4 4-3z" fill="#555"/></svg>120</div>
    <p>To provide personalized, affordable and thorough legal services to every one who needs representation. Attorney Dana Marigold also created</p>
  </article>
  <article class="card" style="left:349px">
    <div class="card-img" role="img" aria-label="Photo of a criminal law book beside a gavel" style="background:linear-gradient(135deg,#2f4f7a,#7f6a52 60%,#4a3426)"></div>
    <h4>CRIMINAL LAW</h4>
    <div class="meta"><svg width="11" height="11" viewBox="0 0 11 11"><rect y="1.5" width="11" height="9.5" fill="#555"/><rect x="1" y="4" width="9" height="6" fill="#fff"/></svg>27 March 2014 <svg style="margin-left:6px" width="13" height="11" viewBox="0 0 13 11"><ellipse cx="6.5" cy="4.5" rx="6.5" ry="4.5" fill="#555"/><path d="M2 7l-1 4 4-3z" fill="#555"/></svg>120</div>
    <p>To provide personalized, affordable and thorough legal services to every one who needs representation. Attorney Dana Marigold also created</p>
  </article>
  <article class="card" style="left:606px">
    <div class="card-img" role="img" aria-label="Photo of letter dice spelling civil on legal books" style="background:linear-gradient(160deg,#2b3f5a,#8b95a3 55%,#e6e2da)"></div>
    <h4>CIVIL LITIGATION</h4>
    <div class="meta"><svg width="11" height="11" viewBox="0 0 11 11"><rect y="1.5" width="11" height="9.5" fill="#555"/><rect x="1" y="4" width="9" height="6" fill="#fff"/></svg>27 March 2014 <svg style="margin-left:6px" width="13" height="11" viewBox="0 0 13 11"><ellipse cx="6.5" cy="4.5" rx="6.5" ry="4.5" fill="#555"/><path d="M2 7l-1 4 4-3z" fill="#555"/></svg>120</div>
    <p>To provide personalized, affordable and thorough legal services to every one who needs representation. Attorney Dana Marigold also created</p>
  </article>
  <article class="card" style="left:870px">
    <div class="card-img" role="img" aria-label="Photo of a hand signing papers under a lawyer heading" style="background:linear-gradient(180deg,#f4f4f2,#cfd3d0 60%,#6f7a72)"></div>
    <h4>ATTORNEY DANA MARIGOLD</h4>
    <div class="meta"><svg width="11" height="11" viewBox="0 0 11 11"><rect y="1.5" width="11" height="9.5" fill="#555"/><rect x="1" y="4" width="9" height="6" fill="#fff"/></svg>27 March 2014 <svg style="margin-left:6px" width="13" height="11" viewBox="0 0 13 11"><ellipse cx="6.5" cy="4.5" rx="6.5" ry="4.5" fill="#555"/><path d="M2 7l-1 4 4-3z" fill="#555"/></svg>120</div>
    <p>To provide personalized, affordable and thorough legal services to every one who needs representation. Attorney Dana Marigold also created</p>
  </article>
</section>

<section class="reviews">
  <h2 class="section-title abs" style="left:100px;top:52px">CLIENT REVIEWS</h2>
  <div class="title-rule abs" style="left:100px;top:95px;width:245px"></div>
  <h2 class="section-title abs" style="left:655px;top:52px">RATINGS AND REVIEWS</h2>
  <div class="title-rule abs" style="left:655px;top:95px;width:348px"></div>

  <blockquote class="quote-box">
    <span class="mark" style="left:12px;top:0">“</span>
    Marigold Law is our go-to source for professional and sound legal advice. Marigold Law has become a vital component to the success of our business as well as the businesses of the clients we have referred to Marigold Law...
    <span class="mark" style="left:345px;top:58px">”</span>
    <svg class="abs" style="left:28px;top:117px" width="20" height="12" viewBox="0 0 20 12"><path d="M0 0h20L8 12z" fill="#f7f7f7" stroke="#e4e4e4"/><path d="M1 0h18" stroke="#f7f7f7" stroke-width="2"/></svg>
  </blockquote>
  <div class="avatar" role="img" aria-label="Portrait photo of the reviewer"></div>
  <div class="reviewer"><b>OAK VALLEY</b>Accounting Professionals</div>

  <div class="ratings-box">
    <div class="badge badge-rating" role="img" aria-label="Attorney rating badge"></div>
    <div class="badge badge-bar" role="img" aria-label="State bar membership badge"></div>
    <div class="badge badge-directory" role="img" aria-label="Lawyer directory listing badge"></div>
  </div>
</section>

<footer class="site-footer">
  <h3 class="foot-head" style="left:100px">QUICK LINKS</h3>
  <ul class="foot-list" style="left:100px">
    <li>Home</li><li>Attorney Profile</li><li>Practice Areas</li><li>Client Reviews</li><li>Links</li><li>Contact Us</li>
  </ul>

  <h3 class="foot-head" style="left:293px">NEWSLETTER</h3>
  <p class="abs" style="left:293px;top:72px;width:230px;font-size:12px;line-height:20px">Register Your email address to get information about us</p>
  <div class="abs" style="left:293px;top:126px;width:264px;height:33px;background:#fff;color:#888;font-size:11.5px;display:flex;align-items:center;padding-left:16px">Email Address</div>
  <div class="btn" style="left:293px;top:178px;width:100px;height:36px">Subscribe</div>

  <h3 class="foot-head" style="left:618px">CONTACT US</h3>
  <div class="foot-contact">
    <div class="row"><svg width="10" height="14" viewBox="0 0 10 14"><path d="M5 0a5 5 0 0 1 5 5c0 4-5 9-5 9S0 9 0 5a5 5 0 0 1 5-5z" fill="#fff"/><circle cx="5" cy="5" r="2" fill="#1e1e1e"/></svg><div>Marigold Law, P.C. Office<br>482 Orchard Avenue<br>Suite 200<br>Chico, CA 95928</div></div>
    <div class="row" style="margin-top:22px"><svg width="12" height="12" viewBox="0 0 24 24"><path fill="#fff" d="M6.6 10.8a15 15 0 0 0 6.6 6.6l2.2-2.2c.3-.3.7-.4 1-.2 1.1.4 2.3.6 3.6.6.6 0 1 .4 1 1V20c0 .6-.4 1-1 1A17 17 0 0 1 3 4c0-.6.4-1 1-1h3.5c.6 0 1 .4 1 1 0 1.3.2 2.5.6 3.6.1.3 0 .7-.2 1z"/></svg>dana@marigoldlawgroup.com</div>
    <div class="row" style="margin-top:23px"><svg width="12" height="12" viewBox="0 0 24 24"><path fill="#fff" d="M6.6 10.8a15 15 0 0 0 6.6 6.6l2.2-2.2c.3-.3.7-.4 1-.2 1.1.4 2.3.6 3.6.6.6 0 1 .4 1 1V20c0 .6-.4 1-1 1A17 17 0 0 1 3 4c0-.6.4-1 1-1h3.5c.6 0 1 .4 1 1 0 1.3.2 2.5.6 3.6.1.3 0 .7-.2 1z"/></svg>(555) 014-2290</div>
    <div class="row" style="margin-top:23px"><svg width="13" height="12" viewBox="0 0 13 12"><rect x="3" width="7" height="4" fill="#fff"/><rect y="4" width="13" height="6" fill="#fff"/><rect x="3" y="8" width="7" height="4" fill="#fff" stroke="#1e1e1e"/></svg>(888) 555-0182</div>
  </div>

  <h3 class="foot-head" style="left:900px">LINKS</h3>
  <ul class="foot-list" style="left:900px">
    <li>www.marigoldwestproperties.com</li><li>www.ledgerbayonline.com</li>
  </ul>

  <div class="bottom-bar"></div>
  <p class="copyright">Copyrights © marigoldlawpc 2016 . All rights reserved. Terms and Conditions &nbsp;|&nbsp; Privacy Policy</p>
  <div class="social" style="left:980px;top:276px">
    <span style="background:#4a67ad"></span><span style="background:#4aa3df"></span><span style="background:#d12121"></span>
  </div>
</footer>

</body>
</html>
```